Business Card for Multi-Brand Sportswear Company

We are looking for a business card which represents our company and the multiple brands within it.

The company: Fen Athletics (LTD)
The brands: Fen, TavaPuni, ElmStretch, Grit and Rain

Employees using these cards would be representing Fen Athletics, rather than any of the individual brands. You will see a current design within the uploaded files, to give some inspiration. The actual text of the brands is not necessary, but the logos should be on there is some format.

Our creative minds on this are stretched, so we are looking for someone to make this their own, and show us what a good business card should look like.

We may like to get these printed with spot gloss, so keep that in mind with your designs.

www.fenathletics.co.uk

Industry/Entity Type

Business

Contact Information for Business Card

Leo Pemberton-Hale
Operations Manager
(+44) 1632 960 418
Leo@fenathletics.co.uk
www.fenathletics.co.uk

Font styles to use
Sans Serif
Other font styles liked:
• Eurostile

Colors
ffffff

Requirements
Nice to have
• Dark (black) background

```html
<!DOCTYPE html>
<html lang="en">
<head>
<meta charset="utf-8">
<title>Fen Athletics – Business Card</title>
<link rel="stylesheet" href="https://fonts.googleapis.com/css2?family=Michroma&family=Titillium+Web:wght@400;600&display=swap">
<style>
  :root {
    --stage: #2e2e2e;
    --card: #0b0b0b;
    --card-front: #141414;
    --white: #ffffff;
    --silver: #b9b9b9;
    --grey-text: #8d8d8d;
    --red: #e3232b;
    --brand-muted: #d9d9d9;
  }
  * { box-sizing: border-box; margin: 0; padding: 0; }
  html, body { width: 1200px; height: 900px; overflow: hidden; }
  body {
    background: var(--stage);
    position: relative;
    font-family: "Titillium Web", Arial, sans-serif;
  }
  .card {
    position: absolute;
    width: 620px;
    height: 354px;
    overflow: hidden;
    box-shadow: 0 10px 30px rgba(0,0,0,0.5);
  }
  .card-art { position: absolute; inset: 0; }

  /* Front */
  .card-front { left: 110px; top: 70px; background: var(--card-front); }
  .front-logo {
    position: absolute;
    left: 0; right: 0; top: 118px;
    text-align: center;
  }
  .front-logo .wordmark {
    font-family: "Michroma", sans-serif;
    font-size: 40px;
    color: var(--silver);
    letter-spacing: 2px;
  }
  .front-logo .tagline {
    font-family: "Michroma", sans-serif;
    font-size: 10px;
    color: var(--grey-text);
    letter-spacing: 4px;
    margin-top: 6px;
  }

  /* Back */
  .card-back { left: 470px; top: 470px; background: var(--card); }
  .back-logo {
    position: absolute;
    left: 40px; top: 52px;
    font-family: "Michroma", sans-serif;
    font-size: 58px;
    color: var(--white);
    letter-spacing: 2px;
  }
  .holder {
    position: absolute;
    right: 30px; top: 42px;
    text-align: right;
  }
  .holder-name {
    font-family: "Michroma", sans-serif;
    font-size: 15px;
    color: var(--white);
  }
  .holder-role {
    font-size: 15px;
    color: var(--red);
    margin-top: 2px;
  }
  .holder-rule {
    position: absolute;
    right: 30px; top: 100px;
    width: 300px; height: 1px;
    background: var(--red);
  }
  .address {
    position: absolute;
    right: 30px; top: 120px;
    text-align: right;
    font-size: 15px;
    line-height: 1.3;
    color: var(--white);
  }
  .brands {
    position: absolute;
    left: 30px; top: 190px;
    display: flex;
    gap: 16px;
    align-items: center;
  }
  .brand {
    display: flex;
    align-items: center;
    gap: 5px;
    font-size: 12px;
    font-weight: 600;
    color: var(--brand-muted);
  }
  .brand-dot { width: 8px; height: 8px; border-radius: 50%; background: var(--red); }
  .contact-rule {
    position: absolute;
    left: 30px; top: 218px;
    width: 240px; height: 1px;
    background: var(--red);
  }
  .contacts {
    position: absolute;
    left: 30px; top: 226px;
    list-style: none;
    font-size: 15px;
    line-height: 1.35;
    color: var(--white);
  }
  .contacts li { display: flex; align-items: center; gap: 8px; }
  .contacts svg { width: 11px; height: 11px; flex: none; }
</style>
</head>
<body>

<section class="card card-front" aria-label="Card front">
  <svg class="card-art" viewBox="0 0 620 354" aria-hidden="true">
    <polygon points="0,328 620,232 620,250 0,350" fill="#ffffff"/>
    <polygon points="0,350 620,250 620,354 0,354" fill="#141414"/>
    <polygon points="300,272 318,269 314,281 296,284" fill="#e3232b"/>
    <polygon points="322,268 340,265 336,277 318,280" fill="#e3232b"/>
    <polygon points="344,264 362,261 358,273 340,276" fill="#e3232b"/>
  </svg>
  <div class="front-logo">
    <div class="wordmark">FEN ATHLETICS</div>
    <div class="tagline">PERFORMANCE WEAR</div>
  </div>
</section>

<section class="card card-back" aria-label="Card back">
  <svg class="card-art" viewBox="0 0 620 354" aria-hidden="true">
    <polygon points="0,330 370,274 366,290 0,354" fill="#e3232b"/>
    <polygon points="376,273 394,270 390,286 372,289" fill="#ffffff"/>
    <polygon points="400,269 430,264 426,280 396,285" fill="#ffffff"/>
    <polygon points="436,263 620,236 620,256 432,279" fill="#e3232b"/>
  </svg>

  <div class="back-logo">FEN</div>

  <div class="holder">
    <div class="holder-name">Leo Pemberton-Hale</div>
    <div class="holder-role">Operations Manager</div>
  </div>
  <div class="holder-rule"></div>
  <div class="address">Fenwick Park, Marston<br>Hollowby, YO9 4DQ</div>

  <div class="brands">
    <span class="brand"><span class="brand-dot"></span>TavaPuni</span>
    <span class="brand">Grit and Rain</span>
    <span class="brand">ElmStretch</span>
  </div>
  <div class="contact-rule"></div>
  <ul class="contacts">
    <li><svg viewBox="0 0 12 12"><circle cx="6" cy="6" r="6" fill="#e3232b"/><path d="M3.6 3.2l1.3-.4.7 1.5-.8.6c.4.8 1 1.4 1.8 1.8l.6-.8 1.5.7-.4 1.3C6.3 8 4 5.7 3.6 3.2z" fill="#0b0b0b"/></svg>(+44) 1632 960 418</li>
    <li><svg viewBox="0 0 12 12"><circle cx="6" cy="6" r="6" fill="#e3232b"/><rect x="3" y="4" width="6" height="4.2" fill="#0b0b0b"/><path d="M3 4l3 2.3L9 4" stroke="#e3232b" stroke-width="0.8" fill="none"/></svg>Leo@fenathletics.co.uk</li>
    <li><svg viewBox="0 0 12 12"><circle cx="6" cy="6" r="6" fill="#e3232b"/><circle cx="6" cy="6" r="3" fill="none" stroke="#0b0b0b" stroke-width="0.9"/><path d="M3 6h6M6 3v6" stroke="#0b0b0b" stroke-width="0.8"/></svg>www.fenathletics.co.uk</li>
  </ul>
</section>

</body>
</html>
```